TREVAL BUILDWORKS, LLC Webpage portfolio

I want to create a Website that allows my potential clients to browse my Skilled work via before and after photos. I want the website to enhance the work that I provide and potentially drive new business, or at least solidify my work.
I also do 3D CAD and Modeling of New Spaces and it would be nice to show some of that work from pencil design to 3D modeling, which I feel may help give me more clients.

The website needs to show a solid carpenter/company with the skills to get any project completed.

Types of Jobs - Custom Carpentry & Finishes, Kitchens, Baths, Basements, Decks, Porches, Whole House Renovation - Skilled Craftsmanship (Hardwood Flooring, Floor and Wall Tile) and much more...

Target Market(s)

Residential Home Renovation, Kitchen and Bath Renovation, Home Improvement

Industry/Entity Type

Residential Construction

Number of Pages Required

5+ page

Font styles to use
Sans Serif
Script

Requirements
Must have
• Similar to Plinvo.com, except for Treval Buildworks.
• Must be inviting.
• My Services Offered
• A way to reach me or contact me for estimates with some sort of Screening Questionare.
Nice to have
• Inviting Colors
Should not have
• Not sure at this time

```html
<!DOCTYPE html>
<html lang="en">
<head>
<meta charset="utf-8">
<title>Treval Buildworks</title>
<link href="https://fonts.googleapis.com/css2?family=Lexend+Exa:wght@200;300;400&family=Questrial&family=Tinos:ital,wght@1,700&display=swap" rel="stylesheet">
<style>
:root{
  --bg:#2a2826;
  --stripe:#1f1d1c;
  --ink:#f2f0ec;
  --muted:#bdb8b0;
  --panel:#0d0d0d;
  --field:#151515;
  --field-line:#2e2e2e;
  --sketch-a:#5a5a5a;
  --sketch-b:#737373;
  --render-a:#5c5c5c;
  --render-b:#4a4a4a;
  --kitchen-a:#6b4a36;
  --kitchen-b:#a89682;
  --dining-a:#3a2a20;
  --dining-b:#5a4534;
  --hall-a:#5e5a55;
  --hall-b:#8a7f76;
  --hall-c:#7a5a48;
  --btn:#2c2c2c;
}
*{margin:0;padding:0;box-sizing:border-box}
html,body{width:1200px;height:2400px;overflow:hidden}
body{
  position:relative;
  background:var(--bg) repeating-linear-gradient(90deg,var(--stripe) 0 3px,transparent 3px 13px);
  color:var(--ink);
  font-family:"Questrial",sans-serif;
}
.abs{position:absolute}
.heading{font-family:"Lexend Exa",sans-serif;font-weight:200;font-size:31px;line-height:43px;letter-spacing:1px;text-transform:uppercase}
.small{font-family:"Lexend Exa",sans-serif;font-weight:300;font-size:10.5px;line-height:14px;text-transform:uppercase}
.phone{left:50px;top:199px;font-size:16px;letter-spacing:.5px}
.brand{left:0;width:1200px;top:215px;text-align:center;font-size:36px;color:var(--muted);font-family:"Questrial",sans-serif}
.brand-mark{display:inline-block;width:22px;height:22px;background:var(--muted);margin-right:12px;vertical-align:-2px}
.social{display:flex;gap:13px}
.social span{width:14px;height:14px;border-radius:50%;background:var(--ink)}
.header-social{left:547px;top:300px}
.nav{right:51px;top:198px;text-align:right;font-size:16px;line-height:43px;letter-spacing:.5px}
.services-media{left:136px;top:400px;width:1013px;height:499px;display:flex}
.services-media .sketch{width:336px;background:linear-gradient(90deg,var(--sketch-a),var(--sketch-b))}
.services-media .render{width:341px;background:linear-gradient(180deg,var(--render-a),var(--render-b))}
.services-media .photo{flex:1;background:linear-gradient(160deg,var(--kitchen-b),var(--kitchen-a) 60%,#3a2a20)}
.services-title{left:50px;top:392px}
.service-list{left:50px;top:548px;width:180px}
.service-list p{margin-bottom:14px}
.service-list .feature{font-size:16px;line-height:22px;margin-bottom:0}
.work-photo{left:282px;top:899px;width:868px;height:650px;background:radial-gradient(ellipse at 70% 80%,var(--dining-b),var(--dining-a) 70%)}
.work-inset{left:136px;top:1000px;width:483px;height:224px;background:linear-gradient(100deg,var(--hall-a) 0%,var(--hall-a) 30%,var(--hall-b) 55%,var(--hall-c))}
.work-title{left:50px;top:994px}
.work-note{left:52px;top:1147px;width:140px}
.work-social{left:139px;top:1284px}
.contact{left:136px;top:1549px;width:1064px;height:851px;background:var(--panel)}
.contact-title{left:50px;top:1592px}
.contact-note{left:50px;width:160px}
.email-label{left:280px;top:1748px;font-size:11px}
.email{left:280px;top:1765px;font-size:18px;letter-spacing:1px}
.intro{left:280px;top:1850px;font-size:10px}
.question{left:280px;font-size:16px;letter-spacing:.5px}
.answer{left:280px;width:542px;height:32px;background:var(--field);border:1px solid var(--field-line);color:#3c3c3c;font-size:15px;padding:6px 10px}
.submit{left:280px;top:2200px;width:136px;height:32px;background:var(--btn);text-align:center;line-height:32px;font-size:15px;letter-spacing:1px}
.estimate{right:51px;top:1742px;text-align:right;font-family:"Lexend Exa",sans-serif;font-weight:200;font-size:50px;line-height:68px}
.clients-label{right:51px;top:1998px;font-size:16px;letter-spacing:.5px;color:var(--muted)}
.avatar{right:51px;width:80px;height:80px;border-radius:50%;background:linear-gradient(135deg,#cfcac4,#6e6a66)}
.avatar.alt{background:linear-gradient(135deg,#5b6ad0,#2d2f6a)}
.client-name{right:51px;font-family:"Tinos",serif;font-style:italic;font-weight:700;font-size:15px;color:var(--muted)}
.client-name small{font-weight:400;font-size:11px}
.footer-social{left:282px;top:2366px}
</style>
</head>
<body>
<header>
  <div class="abs phone">+1 (555) 014-27-90</div>
  <div class="abs brand"><span class="brand-mark"></span>Treval Buildworks</div>
  <div class="abs social header-social" aria-label="Social links"><span></span><span></span><span></span><span></span></div>
  <nav class="abs nav"><div>MY SERVICES</div><div>BROWSE MY WORK</div><div>CONTACT ME</div></nav>
</header>

<section class="services">
  <div class="abs services-media">
    <div class="sketch" role="img" aria-label="Pencil design sketch of a kitchen"></div>
    <div class="render" role="img" aria-label="3D CAD model of the kitchen"></div>
    <div class="photo" role="img" aria-label="Photo of the finished kitchen"></div>
  </div>
  <h2 class="abs heading services-title">My<br>Services</h2>
  <div class="abs small service-list">
    <p>3D CAD modelling of new spaces</p>
    <p>Custom<br>carpentry &amp; finishes,</p>
    <p>Kitchens,<br>baths,<br>basements,<br>decks,<br>porches,</p>
    <p class="feature">Whole house renovation</p>
    <p>Skilled craftsmanship (hardwood flooring, floor and wall tile)</p>
    <p>And much more</p>
  </div>
</section>

<section class="work">
  <div class="abs work-photo" role="img" aria-label="Dining room with granite table after renovation"></div>
  <div class="abs work-inset" role="img" aria-label="Hallway before renovation"></div>
  <h2 class="abs heading work-title">Browse<br>my work</h2>
  <p class="abs small work-note">Brose my work in before and after photos</p>
  <div class="abs social work-social" aria-label="Social links"><span></span><span></span><span></span><span></span></div>
</section>

<section class="abs contact"></section>
<h2 class="abs heading contact-title">Drop us<br>a line</h2>
<p class="abs small contact-note" style="top:1750px">Write to us<br>or<br>respond to the<br>questionnaire</p>
<p class="abs small contact-note" style="top:1896px">Your feedback is very important to us. We'll try our utmost to reply back</p>

<div class="abs email-label">Email us at</div>
<div class="abs email">hello@trevalbuildworks.com</div>
<div class="abs intro">Please spare a moment and answer the following questions</div>
<div class="abs question" style="top:1898px">Lorem ipsum doler sit amet?</div>
<div class="abs answer" style="top:1930px">Your answer</div>
<div class="abs question" style="top:1998px">Lorem ipsum doler sit amet?</div>
<div class="abs answer" style="top:2030px">Your answer</div>
<div class="abs question" style="top:2098px">Lorem ipsum doler sit amet?</div>
<div class="abs answer" style="top:2130px">Your answer</div>
<div class="abs submit">SUBMIT</div>

<div class="abs estimate">REQUEST<br>AN<br>ESTIMATE</div>
<div class="abs clients-label">OUR HAPPY CLIENTS</div>
<div class="abs avatar" style="top:2032px" role="img" aria-label="Client portrait"></div>
<div class="abs client-name" style="top:2112px">Alex Marlow, <small>Entrepreneur</small></div>
<div class="abs avatar alt" style="top:2142px" role="img" aria-label="Client portrait"></div>
<div class="abs client-name" style="top:2222px">Alex Marlow, <small>Entrepreneur</small></div>

<div class="abs social footer-social" aria-label="Social links"><span></span><span></span><span></span><span></span></div>
</body>
</html>
```